4th Generation Family Business Needs a New Card Design!

We are a family owned 4th Generation company. We are based in the Sydney, Australia area and we are desperately in need of a more modern and classy card. We are monumental masons who design, supply & erect lasting memorials throughout cemeteries in Sydney. Our customers are normally in a period of grieving. I have attached logo files that will need to be implemented on the card. Company was established 1935. Australian Owned and Operated. Card needs to be designed to PIXO.com specification.

Target Market(s)

Our target market is based upon people that a grieving for family members that have passed away. We also deal with alot of companies that own and operate cemeteries.

Industry/Entity Type

Business

Contact Information for Business Card

Simon Harcourt, Operations Manager, 0417293086, simon@harcourtmemorials.com.au
Lewis Harcourt, Director, 0491630572, lewis@harcourtmemorials.com.au
Phone # 02 9561 3048
Website: www.harcourtmemorials.com.au
Address: Suite 17, 8 Palfrey Lane, West Carlow, Sydney NSW 2156

Font styles to use
Serif
Decorative
Script

Requirements
Must have
• Would like to see the logo nicely implemented with a modern design. Embossed lettering would be a nice additive.

```html
<!DOCTYPE html>
<html lang="en">
<head>
<meta charset="utf-8">
<title>Harcourt Memorials – Business Card</title>
<link rel="stylesheet" href="https://fonts.googleapis.com/css2?family=Cinzel:wght@500&family=Montserrat:wght@400;600;700&display=swap">
<style>
  :root {
    --ink: #0b0b0b;
    --paper: #ffffff;
    --gold: #f2c12e;
    --stage: #2b2b2b;
    --muted: #e8e8e8;
  }
  * { box-sizing: border-box; margin: 0; padding: 0; }
  html, body { width: 1200px; height: 900px; overflow: hidden; }
  body {
    background: var(--stage);
    position: relative;
    font-family: "Montserrat", sans-serif;
  }
  .card {
    position: absolute;
    width: 540px;
    height: 330px;
    border-radius: 22px;
    overflow: hidden;
    box-shadow: 0 18px 40px rgba(0,0,0,0.5);
  }
  /* Front */
  .card-front {
    left: 70px; top: 80px;
    background: var(--ink);
    display: flex; flex-direction: column; align-items: center; justify-content: center;
  }
  .brand-name {
    font-family: "Cinzel", serif;
    font-weight: 500;
    text-align: center;
    letter-spacing: 3px;
    line-height: 1.05;
  }
  .card-front .brand-name { color: var(--paper); font-size: 44px; }
  .brand-rule {
    width: 250px; height: 2px; background: var(--gold); margin: 14px 0 36px;
  }
  .front-web { color: var(--paper); font-size: 15px; letter-spacing: 0.3px; }
  .front-web .accent { color: var(--gold); font-weight: 600; }

  /* Back */
  .card-back {
    left: 590px; top: 490px;
    background: var(--ink);
  }
  .back-top {
    position: absolute; left: 0; top: 0; width: 100%; height: 148px;
    background: var(--paper);
    border-bottom: 3px solid var(--gold);
    display: flex; flex-direction: column; align-items: center; justify-content: center;
  }
  .card-back .brand-name { color: var(--ink); font-size: 40px; }
  .back-top .brand-rule { margin: 10px 0 0; width: 230px; }
  .back-body {
    position: absolute; left: 0; top: 151px; width: 100%; height: 179px;
    display: flex; align-items: center; justify-content: center;
    padding: 0 26px;
  }
  .person {
    flex: 1; text-align: right; padding-right: 20px; color: var(--paper);
  }
  .person-name { color: var(--gold); font-weight: 700; font-size: 24px; letter-spacing: 0.5px; }
  .person-role { font-size: 14px; margin: 2px 0 14px; }
  .person-address { font-size: 13px; line-height: 1.45; }
  .divider { width: 1px; height: 120px; background: #7a7a7a; }
  .contacts { flex: 1.15; padding-left: 18px; list-style: none; color: var(--paper); font-size: 12.5px; }
  .contacts li { display: flex; align-items: center; gap: 9px; line-height: 1.9; }
  .contacts svg { width: 12px; height: 12px; flex: none; }
  .contacts .accent { color: var(--gold); font-weight: 600; }
</style>
</head>
<body>

<section class="card card-front" aria-label="Card front">
  <h1 class="brand-name">HARCOURT<br>MEMORIALS</h1>
  <div class="brand-rule"></div>
  <p class="front-web">www.<span class="accent">harcourtmemorials</span>.com.au</p>
</section>

<section class="card card-back" aria-label="Card back">
  <header class="back-top">
    <h2 class="brand-name">HARCOURT MEMORIALS</h2>
    <div class="brand-rule"></div>
  </header>
  <div class="back-body">
    <div class="person">
      <p class="person-name">Lewis Harcourt</p>
      <p class="person-role">Director</p>
      <p class="person-address">Suite 17, 8 Palfrey Lane<br>West Carlow, Sydney NSW 2156</p>
    </div>
    <div class="divider"></div>
    <ul class="contacts">
      <li>
        <svg viewBox="0 0 12 12" aria-hidden="true"><rect x="3" y="0.8" width="6" height="10.4" rx="1.2" fill="none" stroke="var(--gold)" stroke-width="1.2"/><circle cx="6" cy="9.2" r="0.7" fill="var(--gold)"/></svg>
        0491630572
      </li>
      <li>
        <svg viewBox="0 0 12 12" aria-hidden="true"><path d="M2.5 1h2l1 2.6-1.3 1a6 6 0 0 0 3.2 3.2l1-1.3 2.6 1v2a1 1 0 0 1-1 1A9.5 9.5 0 0 1 1.5 2a1 1 0 0 1 1-1z" fill="var(--gold)"/></svg>
        02 9561 3048
      </li>
      <li>
        <svg viewBox="0 0 12 12" aria-hidden="true"><rect x="0.8" y="2.2" width="10.4" height="7.6" rx="1" fill="none" stroke="var(--gold)" stroke-width="1.2"/><path d="M1 2.8l5 3.8 5-3.8" fill="none" stroke="var(--gold)" stroke-width="1.2"/></svg>
        lewis@harcourtmemorials.com.au
      </li>
      <li>
        <svg viewBox="0 0 12 12" aria-hidden="true"><circle cx="6" cy="6" r="5" fill="none" stroke="var(--gold)" stroke-width="1.1"/><ellipse cx="6" cy="6" rx="2.2" ry="5" fill="none" stroke="var(--gold)" stroke-width="1"/><path d="M1 6h10" stroke="var(--gold)" stroke-width="1"/></svg>
        <span>www.<span class="accent">harcourtmemorials</span>.com.au</span>
      </li>
    </ul>
  </div>
</section>

</body>
</html>
```